Small Business Broker Business Card Design

A business card design for a small business brokerage, which is a financial service, not unlike real estate brokerage, but for small businesses such as laundromats, pizza shops, restaurants, cleaners etc. The designs should all be simple, more conservative in nature, using the colors and font of the logo. Again, think real estate Brokerage as a business context
Contact Information for Business Card
Name: Glen R. Harlow. Title: Small Business Advisor. Email: g.harlow@bayfieldcapitalworks.example. Mobile: (555) 274-3918. Office: (555) 806-2147. www.bayfieldcapitalworks.example

```html
<!DOCTYPE html>
<html lang="en">
<head>
<meta charset="utf-8">
<title>Bayfield Capital Works — Business Card</title>
<link href="https://fonts.googleapis.com/css2?family=Montserrat:wght@600;700&family=Arimo:wght@400&display=swap" rel="stylesheet">
<style>
  :root {
    --navy: #1d3f72;
    --green: #8cc63f;
    --white: #ffffff;
    --ink: #3a3a3a;
    --muted: #555b63;
    --backdrop: #e9e9e7;
  }
  * { box-sizing: border-box; margin: 0; padding: 0; }
  html, body { width: 1200px; height: 716px; overflow: hidden; }
  body {
    background: var(--backdrop);
    display: flex;
    align-items: center;
    justify-content: center;
    gap: 40px;
    font-family: "Arimo", Arial, sans-serif;
  }
  .card {
    position: relative;
    width: 540px;
    height: 309px;
    overflow: hidden;
    box-shadow: 0 6px 18px rgba(0,0,0,0.18);
  }

  /* Front */
  .card--front {
    background: var(--navy);
    border-bottom: 5px solid var(--green);
    display: flex;
    align-items: center;
    justify-content: center;
  }
  .brand {
    display: flex;
    flex-direction: column;
    align-items: center;
    gap: 8px;
  }
  .brand__name {
    font-family: "Montserrat", Arial, sans-serif;
    font-weight: 700;
    letter-spacing: 0.06em;
    text-transform: uppercase;
    white-space: nowrap;
  }
  .brand__tagline {
    font-family: "Montserrat", Arial, sans-serif;
    font-weight: 600;
    color: var(--green);
    letter-spacing: 0.12em;
    text-transform: uppercase;
    white-space: nowrap;
  }
  .card--front .brand__name { color: var(--white); font-size: 24px; }
  .card--front .brand__tagline { font-size: 11px; }

  /* Back */
  .card--back { background: var(--white); }
  .contact {
    position: absolute;
    left: 34px;
    top: 42px;
  }
  .contact__name {
    font-family: "Montserrat", Arial, sans-serif;
    font-weight: 700;
    font-size: 21px;
    color: var(--navy);
    letter-spacing: 0.03em;
    text-transform: uppercase;
    white-space: nowrap;
  }
  .contact__title {
    font-size: 13px;
    color: var(--muted);
    margin-top: 2px;
    margin-bottom: 18px;
  }
  .contact__list { list-style: none; }
  .contact__item {
    display: flex;
    align-items: center;
    gap: 8px;
    font-size: 12px;
    color: var(--ink);
    line-height: 19px;
    white-space: nowrap;
  }
  .contact__icon { width: 11px; height: 11px; flex: none; }
  .divider {
    position: absolute;
    left: 318px;
    top: 118px;
    width: 1px;
    height: 112px;
    background: var(--navy);
  }
  .card--back .brand {
    position: absolute;
    left: 332px;
    top: 162px;
    align-items: flex-start;
    gap: 5px;
  }
  .card--back .brand__name { color: var(--navy); font-size: 10.5px; letter-spacing: 0.02em; }
  .card--back .brand__tagline { font-size: 6px; letter-spacing: 0.08em; }
  .band {
    position: absolute;
    left: 0; right: 0; bottom: 0;
    height: 11px;
    display: flex;
  }
  .band__navy { width: 37%; background: var(--navy); }
  .band__green { flex: 1; background: var(--green); }
</style>
</head>
<body>

  <section class="card card--front" aria-label="Card front">
    <div class="brand">
      <span class="brand__name">Bayfield Capital Works, Inc</span>
      <span class="brand__tagline">Trusted guidance for every main street sale</span>
    </div>
  </section>

  <section class="card card--back" aria-label="Card back">
    <div class="contact">
      <h1 class="contact__name">Glen R. Harlow</h1>
      <p class="contact__title">Small Business Advisor</p>
      <ul class="contact__list">
        <li class="contact__item">
          <svg class="contact__icon" viewBox="0 0 12 12"><path fill="#8cc63f" d="M1 4c0-2 2-3 5-3s5 1 5 3l-2 1-1-2H4L3 5zM3 6h6l1 5H2z"/></svg>
          (555) 806-2147
        </li>
        <li class="contact__item">
          <svg class="contact__icon" viewBox="0 0 12 12"><rect x="3" y="0.5" width="6" height="11" rx="1" fill="none" stroke="#8cc63f" stroke-width="1.2"/><circle cx="6" cy="9.5" r="0.7" fill="#8cc63f"/></svg>
          (555) 274-3918
        </li>
        <li class="contact__item">
          <svg class="contact__icon" viewBox="0 0 12 12"><rect x="0.5" y="2.5" width="11" height="7" fill="#8cc63f"/><path d="M0.5 2.5 6 7l5.5-4.5" fill="none" stroke="#fff" stroke-width="1"/></svg>
          g.harlow@bayfieldcapitalworks.example
        </li>
        <li class="contact__item">
          <svg class="contact__icon" viewBox="0 0 12 12"><circle cx="6" cy="6" r="5.2" fill="none" stroke="#8cc63f" stroke-width="1.2"/><path d="M1 6h10M6 1c-2.5 3-2.5 7 0 10M6 1c2.5 3 2.5 7 0 10" fill="none" stroke="#8cc63f" stroke-width="0.9"/></svg>
          www.bayfieldcapitalworks.example
        </li>
      </ul>
    </div>

    <div class="divider"></div>

    <div class="brand">
      <span class="brand__name">Bayfield Capital Works, Inc</span>
      <span class="brand__tagline">Trusted guidance for every main street sale</span>
    </div>

    <div class="band">
      <span class="band__navy"></span>
      <span class="band__green"></span>
    </div>
  </section>

</body>
</html>
```